Business Card Design

Online clothing womens clothing store, I sell my clothing online and at the markets.

i would like the attached picture on the front of the card and the contact information on the back.

Industry/Entity Type

Business

Contact Information for Business Card

Marlow Thread
Karen Whitfield
(Instagram symbol) _marlow_thread_
(Facebook symbol) www.fakebookexample.com/marlowthreadau/

W : www.marlowthread.example.au
E : info@marlowthread.example.au
P : 0498716204

```html
<!DOCTYPE html>
<html lang="en">
<head>
<meta charset="UTF-8">
<title>Marlow Thread — Business Card</title>
<link href="https://fonts.googleapis.com/css2?family=Source+Sans+3:wght@400;600;700&display=swap" rel="stylesheet">
<style>
  :root {
    --bg-top: #2b2b2b;
    --bg-bottom: #040404;
    --card: #ffffff;
    --ink: #111111;
    --muted: #555555;
    --icon: #1a1a1a;
    --photo-light: #e4e8e8;
    --photo-mid: #b9c6c6;
    --photo-dark: #5f6a6c;
    --logo-text: #ffffff;
  }
  * { box-sizing: border-box; margin: 0; padding: 0; }
  html, body {
    width: 1200px; height: 900px; overflow: hidden;
  }
  body {
    background: linear-gradient(180deg, var(--bg-top) 0%, #1a1a1a 45%, var(--bg-bottom) 100%);
    font-family: "Source Sans 3", "Myriad Pro", Arial, sans-serif;
    position: relative;
  }
  .card {
    position: absolute;
    background: var(--card);
    border-radius: 12px;
  }
  .card--back { left: 149px; top: 306px; width: 439px; height: 271px; }
  .card--front { left: 608px; top: 306px; width: 441px; height: 272px; }

  .holder-name {
    position: absolute; left: 0; right: 0; top: 78px;
    text-align: center;
    font-size: 23px; font-weight: 700; color: var(--ink);
    letter-spacing: 0.1px;
  }

  .social {
    position: absolute; left: 44px; top: 178px;
    list-style: none;
  }
  .social li {
    display: flex; align-items: center; gap: 4px;
    font-size: 12.5px; color: var(--muted); line-height: 16px;
  }
  .social .mark {
    width: 9px; height: 9px; background: var(--icon); border-radius: 2px;
    display: inline-block;
  }

  .contact {
    position: absolute; right: 42px; top: 165px;
    list-style: none; text-align: right;
  }
  .contact li {
    display: flex; justify-content: flex-end; align-items: center; gap: 7px;
    font-size: 12.5px; color: var(--muted); line-height: 16px;
  }
  .contact svg { width: 10px; height: 10px; fill: var(--icon); flex: none; }

  .front-photo {
    position: absolute; left: 72px; top: 36px; width: 297px; height: 201px;
    background:
      radial-gradient(ellipse 55% 70% at 72% 55%, var(--photo-dark) 0%, rgba(95,106,108,0.5) 45%, rgba(185,198,198,0) 75%),
      linear-gradient(135deg, var(--photo-light) 0%, var(--photo-mid) 100%);
    box-shadow: 2px 4px 8px rgba(0,0,0,0.55);
    border: 1px solid #9aa3a3;
    overflow: hidden;
  }
  .brand-name {
    position: absolute; left: 18px; right: 12px; bottom: 18px;
    font-size: 31px; font-weight: 600; color: var(--logo-text);
    letter-spacing: 1px; text-transform: uppercase; white-space: nowrap;
    line-height: 1; text-align: center;
  }
</style>
</head>
<body>

  <section class="card card--back" aria-label="Card back with contact details">
    <h1 class="holder-name">Karen Whitfield</h1>

    <ul class="social">
      <li><span class="mark"></span>_marlow_thread_</li>
      <li><span class="mark"></span>/marlowthreadau/</li>
    </ul>

    <ul class="contact">
      <li>0498716204
        <svg viewBox="0 0 10 10" aria-hidden="true"><path d="M1 3.2C1 2 3 1.5 5 1.5S9 2 9 3.2V4H7V3.3H3V4H1Z M2.2 4.5h5.6L9 8.5H1Z"/></svg>
      </li>
      <li>info@marlowthread.example.au
        <svg viewBox="0 0 10 10" aria-hidden="true"><path d="M1 2h8v6H1Z" /><path d="M1.3 2.4 5 5.4l3.7-3" fill="none" stroke="#fff" stroke-width="0.9"/></svg>
      </li>
      <li>www.marlowthread.example.au
        <svg viewBox="0 0 10 10" aria-hidden="true"><path d="M4.2 5.8 5.8 4.2M3.4 4.8 2 6.2a1.4 1.4 0 0 0 2 2l1.4-1.4M6.6 5.2 8 3.8a1.4 1.4 0 0 0-2-2L4.6 3.2" fill="none" stroke="#1a1a1a" stroke-width="1.1" stroke-linecap="round"/></svg>
      </li>
    </ul>
  </section>

  <section class="card card--front" aria-label="Card front">
    <div class="front-photo" role="img" aria-label="Misty blue-grey fashion photograph of a woman in profile">
      <span class="brand-name">Marlow Thread</span>
    </div>
  </section>

</body>
</html>
```